Give Gold Kite an Online Presence!

Gold Kite Property Maintenance is an Australian Owned property maintenance company who needs a stand out online presence.

GK maintains many buildings and sites and wants to appeal to a corporate professional market with their brand new website. GK is essentially a handyman service offering all maintenance services to home owners, office managers, real estate agents and strata managers.

The Website:
We need a corporate website that appeals to our broader customer base (property owners, property managers, office managers) the copy is being written by a professional so use filler text for now.

Things that we want:
Home page that sets us apart and appeals to the corporate and residential market. The home page needs to not focus on either the residential or commercial market. The home page should focus on our logo and branding. We have a logo already and it is attached to the brief, please use it and try to consider the colour pallette that goes with it. Whilst we want the site to appear strong and manly it is important to remember that 95% of our customers are female so we need the site to be appealing to women. Women need to believe that we are strong, dependable and trustworthy.
We'd like a quote page and potentially also the ability to get a quote from the home page (please don't put it in if it ruins the overall feel of the home page)
An "about us" page
A contact us page
A blog that's built in (we don't want to link to an external blog)
(overall we'd expect to have 6 or 7 pages total)

The site will also need coding - we expect this to be done in a separate project but need you to consider a few things about the coding side of things.

It needs to be iPhone and iPad compatible.

We'd like you to suggest the best CMS that you would use or if you would suggest not using a CMS please let us know with your submissions.

Target Market(s)

Property owners, office managers and property managers who need maintenance on buildings (So all of them)

Industry/Entity Type

Property Maintenance

Requirements
Must have
• Our Logo
Home page
About Us
Residential
Commercial
Real Estate/Strata
Contact Us/Quote
Blog
Nice to have
• Quote form included in home page
Movement on the home page at least
Should not have
• other logos, too much colour
NO FLASH

```html
<!DOCTYPE html>
<html lang="en">
<head>
<meta charset="utf-8">
<title>Gold Kite Property Maintenance</title>
<link rel="stylesheet" href="https://fonts.googleapis.com/css2?family=Arimo:ital,wght@0,400;0,700;1,400&display=swap">
<style>
:root{
  --orange:#f39a2b;
  --orange-light:#f8b04a;
  --orange-dark:#e5851c;
  --charcoal:#4a4a4a;
  --charcoal-dark:#3a3a3a;
  --text:#555555;
  --heading:#333333;
  --rule:#7a7a7a;
  --accent-blue:#1a9fcf;
  --white:#ffffff;
}
*{box-sizing:border-box;margin:0;padding:0}
html,body{width:1200px;height:962px;overflow:hidden;background:var(--white)}
body{position:relative;font-family:"Arimo",Arial,sans-serif;color:var(--text)}
.abs{position:absolute}

/* top strip & nav */
.top-strip{left:120px;top:0;width:960px;height:19px;background:linear-gradient(90deg,var(--orange) 0,var(--orange) 70%,var(--charcoal) 71%)}
.main-nav{left:120px;top:19px;width:960px;height:41px;background:linear-gradient(#ffffff,#ececec);display:flex;align-items:center}
.nav-item{height:41px;display:flex;align-items:center;justify-content:center;font-size:12px;color:#444;border-right:1px solid #d4d4d4;text-transform:uppercase}
.nav-item.active{color:var(--orange);background:linear-gradient(90deg,#fff,#f4f4f4)}
.badge-new{background:#1d6fb5;color:#fff;font-size:9px;font-weight:700;border-radius:8px;padding:2px 5px;margin-right:8px}
.search-area{left:913px;top:19px;width:167px;height:41px;background:#fff;border-left:1px solid #ddd}
.search-box{left:920px;top:25px;width:126px;height:28px;border:1px solid #c8c8c8;font-size:11px;font-style:italic;color:#333;padding:7px 8px}

/* hero */
.hero{left:120px;top:60px;width:960px;height:244px;background:linear-gradient(135deg,var(--orange-light),var(--orange) 50%,var(--orange-dark))}
.hero-shadow{left:140px;top:304px;width:920px;height:16px;background:radial-gradient(ellipse at top,rgba(0,0,0,.25),rgba(0,0,0,0) 70%)}
.brand{left:145px;top:232px;width:210px;height:48px;display:flex;flex-direction:column;align-items:center;justify-content:center;color:var(--white);font-weight:700;text-transform:uppercase;line-height:1}
.brand-name{font-size:22px}
.brand-sub{font-size:13px;margin-top:4px}
.headline{left:392px;top:112px;font-size:92px;font-weight:700;color:var(--white);letter-spacing:-1px;text-shadow:2px 3px 4px rgba(0,0,0,.3)}
.subline{left:393px;top:200px;font-size:17px;font-weight:700;color:var(--white);text-transform:uppercase}
.subline-2{left:393px;top:220px;font-size:16px;font-style:italic;color:var(--white);text-transform:uppercase}

.quote-card{left:839px;top:82px;width:215px;height:123px;background:#2f2f2f;border-radius:8px}
.quote-inner{left:847px;top:90px;width:199px;height:106px;border-radius:6px;background:linear-gradient(#f4f4f4,#bdbdbd)}
.quote-title{left:847px;top:96px;width:199px;text-align:center;font-size:11px;font-weight:700;color:#333}
.quote-field{left:860px;width:173px;height:30px;border-radius:8px;background:#fff;border:1px solid #ccc;font-size:11px;font-style:italic;color:#666;padding:8px 9px}
.quote-btn{left:843px;top:242px;width:202px;height:36px;border-radius:18px;background:linear-gradient(#fbbf4d,#f08d1a);color:#fff;font-weight:700;font-size:16px;display:flex;align-items:center;justify-content:center;text-shadow:1px 1px 2px rgba(0,0,0,.35);box-shadow:0 2px 4px rgba(0,0,0,.4)}

/* body copy */
.copy{font-size:12px;line-height:14.5px;color:var(--text);text-align:justify;text-align-last:justify}
.section-title{left:116px;top:402px;width:960px;display:flex;align-items:center;gap:20px}
.section-title .rule{flex:1;height:2px;background:var(--rule)}
.section-title h2{font-weight:400;font-size:25px;color:#7a7a7a;text-transform:uppercase;letter-spacing:.3px}
.divider{left:117px;top:522px;width:960px;height:1px;background:#c8c8c8;box-shadow:0 3px 6px rgba(0,0,0,.08)}

/* services */
.service-photo{top:555px;height:199px}
.service-title{top:764px;text-align:center;font-size:22px;font-weight:700;color:var(--heading)}
.service-num{top:792px;font-size:62px;font-weight:700;color:var(--accent-blue);line-height:1}
.service-text{top:802px;width:256px}
</style>
</head>
<body>

<div class="abs top-strip"></div>
<nav class="abs main-nav">
  <div class="nav-item active" style="width:71px">Start</div>
  <div class="nav-item" style="width:97px">About Us</div>
  <div class="nav-item" style="width:110px">Residential</div>
  <div class="nav-item" style="width:109px">Commercial</div>
  <div class="nav-item" style="width:155px">Real Estate/Strata</div>
  <div class="nav-item" style="width:149px">Contact Us/Quote</div>
  <div class="nav-item" style="width:102px;border-right:none"><span class="badge-new">NEW</span>Blog</div>
</nav>
<div class="abs search-area"></div>
<div class="abs search-box">Search...</div>
<svg class="abs" style="left:1056px;top:31px" width="16" height="16" viewBox="0 0 16 16" aria-hidden="true">
  <circle cx="6.5" cy="6.5" r="4.5" fill="none" stroke="#3a8fd0" stroke-width="2"/>
  <line x1="10" y1="10" x2="14" y2="14" stroke="#3a8fd0" stroke-width="2.4" stroke-linecap="round"/>
</svg>

<header class="abs hero">
  <svg class="abs" style="left:0;top:0" width="960" height="244" viewBox="0 0 960 244" aria-hidden="true">
    <defs>
      <linearGradient id="panel" x1="0" y1="0" x2="1" y2="1">
        <stop offset="0" stop-color="#555"/>
        <stop offset="1" stop-color="#3c3c3c"/>
      </linearGradient>
    </defs>
    <path d="M690 0 C660 40 700 90 665 140 C640 180 630 220 635 244 L960 244 L960 0 Z" fill="url(#panel)"/>
  </svg>
</header>
<div class="abs" role="img" aria-label="Skyline and silhouettes of three tradesmen behind the brand name" style="left:160px;top:80px;width:180px;height:150px;border-radius:6px;background:linear-gradient(rgba(50,40,30,.35),rgba(50,40,30,.15))"></div>
<div class="abs brand" style="background:var(--orange-dark);border-radius:6px">
  <span class="brand-name">Gold Kite</span>
  <span class="brand-sub">Property Maintenance</span>
</div>
<div class="abs headline">SIMPLY</div>
<div class="abs subline">The best property maintenance</div>
<div class="abs subline-2">You can get anywhere</div>

<div class="abs quote-card"></div>
<svg class="abs" style="left:932px;top:204px" width="20" height="13" viewBox="0 0 20 13" aria-hidden="true"><path d="M0 0 L20 0 L10 13 Z" fill="#2f2f2f"/></svg>
<div class="abs quote-inner"></div>
<div class="abs quote-title">Request a quote now!</div>
<div class="abs quote-field" style="top:118px">Your E-mail</div>
<div class="abs quote-field" style="top:156px">Your Property type</div>
<div class="abs quote-btn">REQUEST QUOTE</div>
<div class="abs hero-shadow"></div>

<p class="abs copy" style="left:119px;top:343px;width:954px">Lorem ipsum dolor sit amet, consectetur adipisicing elit. Proin nibh augue, suscipit a, scelerisque sed, lacinia in, mi. Cras vel lorem. Etiam pellentesque aliquetLorem ipsum dolor sit amet, consectetur adipisicing elit. Proin nibh augue, suscipit a, scelerisque sed, lacinia in, mi. Cras vel lorem. Etiam pellentesque aliquetLorem ipsum dolor sit amet, consectetur adip-isicing elit. Proin nibh augue, suscipit a, scelerisque sed, lacinia in, mi. Cras vel lorem. Etiam pellentesque aliquetLorem ipsum dolor sit amet, consectetur adipisicing elit. Proin nibh</p>

<div class="abs section-title"><span class="rule"></span><h2>Lorem ipsum dolor sit am contestadur</h2><span class="rule"></span></div>

<p class="abs copy" style="left:119px;top:447px;width:954px">Lorem ipsum dolor sit amet, consectetur adipisicing elit. Proin nibh augue, suscipit a, scelerisque sed, lacinia in, mi. Cras vel lorem. Etiam pellentesque aliquetLorem ipsum dolor sit amet, consectetur adipisicing elit. Proin nibh augue, suscipit a, scelerisque sed, lacinia in, mi. Cras vel lorem. Etiam pellentesque aliquetLorem ipsum dolor sit amet, consectetur adip-isicing elit. Proin nibh augue, suscipit a, scelerisque sed, lacinia in, mi. Cras vel lorem. Etiam pellentesque aliquetLorem ipsum dolor sit amet, consectetur adipisicing elit. Proin nibh</p>

<div class="abs divider"></div>

<div class="abs service-photo" role="img" aria-label="Builders reviewing plans under a timber roof frame" style="left:123px;width:295px;background:linear-gradient(160deg,#6f8fb8,#b98a5a 55%,#8a5e34)"></div>
<div class="abs service-photo" role="img" aria-label="Technician inspecting pipes and gauges in a plant room" style="left:450px;width:300px;background:linear-gradient(160deg,#8a8f96,#5f6570 55%,#3d4450)"></div>
<div class="abs service-photo" role="img" aria-label="Site engineers in hard hats reading plans at a steel frame" style="left:782px;width:297px;background:linear-gradient(160deg,#2f5fa8,#6d8fc2 50%,#a7a29a)"></div>

<h3 class="abs service-title" style="left:123px;width:295px">Construction</h3>
<h3 class="abs service-title" style="left:457px;width:300px">Maintenance</h3>
<h3 class="abs service-title" style="left:782px;width:297px">And more</h3>

<div class="abs service-num" style="left:122px">1</div>
<div class="abs service-num" style="left:450px">2</div>
<div class="abs service-num" style="left:782px">3</div>

<p class="abs copy service-text" style="left:166px">Lorem ipsum dolor sit amet, consectetur adipis-icing elit. Proin nibh augue, suscipit a, sceleris-que sed, lacinia in, mi. Cras vel lorem. Etiam</p>
<p class="abs copy service-text" style="left:501px;width:251px">Lorem ipsum dolor sit amet, consectetur adipis-icing elit. Proin nibh augue, suscipit a, sceleris-que sed, lacinia in, mi. Cras vel lorem. Etiam</p>
<p class="abs copy service-text" style="left:832px;width:251px">Lorem ipsum dolor sit amet, consectetur adipis-icing elit. Proin nibh augue, suscipit a, sceleris-que sed, lacinia in, mi. Cras vel lorem. Etiam</p>

<p class="abs copy" style="left:126px;top:865px;width:953px">Lorem ipsum dolor sit amet, consectetur adipisicing elit. Proin nibh augue, suscipit a, scelerisque sed, lacinia in, mi. Cras vel lorem. Etiam pellentesque aliquetLorem ipsum dolor sit amet, consectetur adipisicing elit. Proin nibh augue, suscipit a, scelerisque sed, lacinia in, mi. Cras vel lorem. Etiam pellentesque aliquetLorem ipsum dolor sit amet, consectetur adip-isicing elit. Proin nibh augue, suscipit a, scelerisque sed, lacinia in, mi. Cras vel lorem. Etiam pellentesque aliquetLorem ipsum dolor sit amet, consectetur adipisicing elit. Proin nibh</p>

</body>
</html>
```